need corporate, modern business card created for Consulting Company

I need a slick business card using elements from my website, as well as, integrating my pixelforge-created logo (see files).

The business card needs to be:
1. Corporate and modern
2. Clean and professional

I've included a PSD with the logo/icon that you can use to create it. Feel free to try a metallic finish on the logo, make it bigger/small, underlay it. Whatever you need to do to make my card stand out.

Try a black background, or white background or gray.

The idea is for my card to be memorable as well as professional and corporate.

Target Market(s)

Corporate business in the US and Canada.

Industry/Entity Type

Business

Contact Information for Business Card

Commerce Advancing Methods
Martin Coles, Senior Partner
office: 1 877 555 0143
mobile: 1 519 555 0172
website: http://www.brightvale.example

Requirements
Must have
• Card-related information
• corporate, yet modern
• clean and professional
• incorporate the icon only
• must have an editable form when complete!
Nice to have
• metallic icon might be cool
• try it with white or black

```html
<!DOCTYPE html>
<html lang="en">
<head>
<meta charset="utf-8">
<title>Brightvale Business Card</title>
<link rel="stylesheet" href="https://fonts.googleapis.com/css2?family=Tinos:wght@400;700&display=swap">
<style>
  :root {
    --page: #e9e7e4;
    --card-black: #232323;
    --brand-blue: #2f6cc0;
    --swoosh-gray: #a7a7a9;
    --ink-white: #ffffff;
    --shadow: rgba(0, 0, 0, 0.22);
  }
  * { margin: 0; padding: 0; box-sizing: border-box; }
  html, body {
    width: 1200px;
    height: 900px;
    overflow: hidden;
    background: var(--page);
    font-family: "Tinos", "Times New Roman", serif;
  }
  .canvas {
    position: relative;
    width: 1200px;
    height: 900px;
    display: flex;
    flex-direction: column;
    align-items: center;
    justify-content: center;
    gap: 44px;
  }
  .card {
    position: relative;
    width: 630px;
    height: 360px;
    border-radius: 30px;
    overflow: hidden;
    background: var(--card-black);
    box-shadow: 0 12px 30px var(--shadow);
  }
  .card__art {
    position: absolute;
    inset: 0;
    width: 100%;
    height: 100%;
  }
  .brand {
    position: absolute;
    display: flex;
    align-items: center;
    gap: 12px;
    color: var(--brand-blue);
    font-weight: 700;
    letter-spacing: 0.5px;
  }
  .brand__mark {
    width: 22px;
    height: 22px;
    background: var(--brand-blue);
  }
  .card--back .brand {
    left: 50%;
    top: 50%;
    transform: translate(-50%, -50%);
    font-size: 58px;
  }
  .card--back .brand__mark { width: 30px; height: 30px; }
  .card--front .brand {
    left: 300px;
    top: 118px;
    font-size: 50px;
  }
  .holder {
    position: absolute;
    left: 370px;
    top: 228px;
    width: 200px;
    text-align: center;
    color: var(--ink-white);
  }
  .holder__name { font-size: 24px; line-height: 1.25; }
  .holder__title { font-size: 20px; line-height: 1.3; }
  .contacts {
    position: absolute;
    left: 22px;
    top: 200px;
    list-style: none;
    color: var(--ink-white);
    font-size: 13.5px;
    line-height: 1.2;
  }
  .contacts__item {
    display: flex;
    align-items: flex-start;
    gap: 7px;
    margin-bottom: 8px;
  }
  .contacts__icon { flex: none; width: 12px; height: 12px; margin-top: 1px; }
</style>
</head>
<body>
<main class="canvas">

  <section class="card card--back" aria-label="Card back">
    <div class="brand">
      <span class="brand__mark"></span>
      <span class="brand__name">brightvale</span>
    </div>
  </section>

  <section class="card card--front" aria-label="Card front">
    <svg class="card__art" viewBox="0 0 630 360" preserveAspectRatio="none" aria-hidden="true">
      <path fill="var(--swoosh-gray)" d="M0,360 L0,58 C100,18 190,8 258,52 C365,126 372,286 630,312 L630,360 Z"/>
      <path fill="var(--card-black)" d="M0,360 L0,66 C96,28 184,18 246,60 C350,132 356,296 630,326 L630,360 Z"/>
      <path fill="var(--swoosh-gray)" d="M0,360 L0,74 C92,38 176,28 236,68 C338,138 344,304 630,338 L630,360 Z"/>
      <path fill="var(--brand-blue)" d="M0,360 L0,82 C88,46 168,38 226,76 C326,144 332,312 630,352 L630,360 Z"/>
    </svg>

    <div class="brand">
      <span class="brand__mark"></span>
      <span class="brand__name">brightvale</span>
    </div>

    <div class="holder">
      <p class="holder__name">Evan Porter</p>
      <p class="holder__title">Owner / C.E.O</p>
    </div>

    <ul class="contacts">
      <li class="contacts__item">
        <svg class="contacts__icon" viewBox="0 0 12 12" aria-hidden="true"><circle cx="6" cy="6" r="6" fill="var(--ink-white)"/><path d="M6 2.5a2.2 2.2 0 0 0-2.2 2.2C3.8 6.5 6 9.5 6 9.5s2.2-3 2.2-4.8A2.2 2.2 0 0 0 6 2.5z" fill="var(--brand-blue)"/></svg>
        <span>Suite # 410, Elm Bldg,<br>NY 10027</span>
      </li>
      <li class="contacts__item">
        <svg class="contacts__icon" viewBox="0 0 12 12" aria-hidden="true"><circle cx="6" cy="6" r="6" fill="var(--ink-white)"/><path d="M3.6 3c.6-.4 1 .1 1.3.7.2.4 0 .7-.3 1 .3.8.9 1.4 1.7 1.7.3-.3.6-.5 1-.3.6.3 1.1.7.7 1.3-.5.8-1.5.9-2.6.2C4.5 6.9 3.8 6 3.3 5c-.5-1-.4-1.6.3-2z" fill="var(--brand-blue)"/></svg>
        <span>212-555-0148<br>212-555-0193<br>212-555-0116</span>
      </li>
      <li class="contacts__item">
        <svg class="contacts__icon" viewBox="0 0 12 12" aria-hidden="true"><circle cx="6" cy="6" r="6" fill="var(--ink-white)"/><rect x="3" y="4" width="6" height="4.2" fill="var(--brand-blue)"/><path d="M3 4l3 2.4L9 4" stroke="var(--ink-white)" stroke-width="0.7" fill="none"/></svg>
        <span>name@brightvale.example</span>
      </li>
      <li class="contacts__item">
        <svg class="contacts__icon" viewBox="0 0 12 12" aria-hidden="true"><circle cx="6" cy="6" r="6" fill="var(--ink-white)"/><circle cx="6" cy="6" r="3.2" fill="none" stroke="var(--brand-blue)" stroke-width="0.9"/><path d="M2.8 6h6.4M6 2.8c-1.4 1.8-1.4 4.6 0 6.4M6 2.8c1.4 1.8 1.4 4.6 0 6.4" stroke="var(--brand-blue)" stroke-width="0.7" fill="none"/></svg>
        <span>www.brightvale.example</span>
      </li>
    </ul>
  </section>

</main>
</body>
</html>
```